Spiritual Healing bussiness needs logo/business card

Simple, clean looking logo/card
For spiritual business with healing services and occult rituals

Contact Information for Business Card

Needs my name: Tobin Varley
Business name: Lantern Healing Shop
Services provided and worded in this way:

Reiki Healing
Tarot
Oils
Rituals Of Change

Can look occult like but with light energy.

Colors
0255a3
3276b5
85abd2
33a6d7
85cae6
0292cd

```html
<!DOCTYPE html>
<html lang="en">
<head>
<meta charset="utf-8">
<title>Lantern Healing Shop – Business Card</title>
<link rel="stylesheet" href="https://fonts.googleapis.com/css2?family=Arvo&family=Lato:wght@400&display=swap">
<style>
  :root {
    --navy: #0255a3;
    --sky: #0292cd;
    --sky-soft: #85cae6;
    --white: #ffffff;
    --backdrop: #5b5b5b;
    --rule: rgba(255, 255, 255, 0.35);
  }
  * { margin: 0; padding: 0; box-sizing: border-box; }
  html, body {
    width: 1200px;
    height: 802px;
    overflow: hidden;
    background: var(--backdrop);
  }
  .canvas {
    position: relative;
    width: 1200px;
    height: 802px;
  }
  .card {
    position: absolute;
    top: 274px;
    width: 442px;
    height: 265px;
    overflow: hidden;
  }
  .card--front { left: 136px; background: var(--navy); }
  .card--back { left: 624px; background: var(--white); }

  .emblem-area {
    position: absolute;
    left: 0;
    top: 0;
    width: 240px;
    height: 265px;
    background: linear-gradient(160deg, var(--sky) 0%, var(--sky-soft) 100%);
  }

  .front-text {
    position: absolute;
    right: 20px;
    top: 0;
    text-align: right;
    color: var(--white);
  }
  .shop-name {
    position: absolute;
    right: 0;
    top: 34px;
    white-space: nowrap;
    font-family: "Arvo", serif;
    font-size: 20px;
    letter-spacing: 0.2px;
  }
  .person-name {
    position: absolute;
    right: 0;
    top: 106px;
    white-space: nowrap;
    font-family: "Arvo", serif;
    font-size: 17px;
  }
  .contact-list {
    position: absolute;
    right: 0;
    top: 137px;
    list-style: none;
    font-family: "Lato", sans-serif;
    font-size: 12.5px;
    line-height: 17px;
  }
  .contact-list li {
    display: flex;
    justify-content: flex-end;
    align-items: center;
    gap: 3px;
    white-space: nowrap;
  }
  .contact-icon { width: 15px; height: 15px; flex: none; }
  .divider {
    position: absolute;
    right: 0;
    top: 196px;
    width: 182px;
    height: 1px;
    background: var(--rule);
  }
  .service-list {
    position: absolute;
    right: 0;
    top: 201px;
    list-style: none;
    font-family: "Lato", sans-serif;
    font-size: 12.5px;
    line-height: 16.3px;
    white-space: nowrap;
  }
  .dot {
    display: inline-block;
    width: 6px;
    height: 6px;
    border-radius: 50%;
    background: var(--white);
    margin: 0 2px 1px 4px;
    vertical-align: middle;
  }

  .brand-dot {
    position: absolute;
    left: 191px;
    top: 75px;
    width: 60px;
    height: 60px;
    border-radius: 50%;
    background: var(--navy);
  }
  .brand-name {
    position: absolute;
    left: 0;
    right: 0;
    top: 174px;
    text-align: center;
    font-family: "Arvo", serif;
    font-size: 25px;
    color: var(--navy);
  }
</style>
</head>
<body>
<main class="canvas">

  <section class="card card--front">
    <div class="emblem-area" role="img" aria-label="Heart-shaped healing emblem with a figure's round head above it"></div>

    <div class="front-text">
      <h1 class="shop-name">Lantern Healing Shop</h1>
      <h2 class="person-name">Tobin Varley</h2>

      <ul class="contact-list">
        <li>061-482 730 155
          <svg class="contact-icon" viewBox="0 0 16 16" aria-hidden="true">
            <circle cx="8" cy="8" r="7" fill="none" stroke="#fff" stroke-width="1.2"/>
            <path d="M4.5 7.2c0-1.3 7-1.3 7 0v1h-2v-1h-3v1h-2z M5.5 8.8h5l.8 2.7H4.7z" fill="#fff"/>
          </svg>
        </li>
        <li>hello@lanternhealing.net
          <svg class="contact-icon" viewBox="0 0 16 16" aria-hidden="true">
            <circle cx="8" cy="8" r="7" fill="none" stroke="#fff" stroke-width="1.2"/>
            <rect x="4.3" y="5.3" width="7.4" height="5.4" rx="0.8" fill="#fff"/>
            <path d="M4.6 5.7 8 8.4l3.4-2.7" fill="none" stroke="#0255a3" stroke-width="0.9"/>
          </svg>
        </li>
        <li>www.LanternHealingShop.net
          <svg class="contact-icon" viewBox="0 0 16 16" aria-hidden="true">
            <circle cx="8" cy="8" r="7" fill="none" stroke="#fff" stroke-width="1.2"/>
            <circle cx="8" cy="8" r="4.2" fill="#fff"/>
            <path d="M8 3.8v8.4M3.8 8h8.4M8 3.8c-2 2.3-2 6.1 0 8.4M8 3.8c2 2.3 2 6.1 0 8.4" fill="none" stroke="#0255a3" stroke-width="0.7"/>
          </svg>
        </li>
      </ul>

      <div class="divider"></div>

      <ul class="service-list">
        <li>Reiki Healing<span class="dot"></span></li>
        <li>Tarot<span class="dot"></span>Oils<span class="dot"></span></li>
        <li>Rituals Of Change<span class="dot"></span></li>
      </ul>
    </div>
  </section>

  <section class="card card--back">
    <div class="brand-dot"></div>
    <p class="brand-name">Lantern Healing Shop</p>
  </section>

</main>
</body>
</html>
```